Redesign of the UI of a customer service platform

To improve the user experience of our customers, we need a new design for our agent interface of our customer service platform (helpnook.com).
The focus will be on the dashboard and the inbox screens (see attached) along with the common UI elements (Buttons, menu, fonts, forms...)
We want a simple and distinctive design

Target Market(s)

Worldwide

Industry/Entity Type

It Service

Number of Pages Required

3 page

Font styles to use
Sans Serif

Requirements
Must have
• New Onboarding page: this is a new page that is shown to user the first time they login to the platform. This will replace the current onboarding screen (setup SMS, Setup widget...etc)
• Dashboard page: to access important information and activate services (see screenshot from current site)
• Inbox page: to manage all the interactions with customers. (see screenshot from current site)
• UI elements (buttons, menus, forms, tables, fonts, color palette)

```html
<!DOCTYPE html>
<html lang="en">
<head>
<meta charset="utf-8">
<title>helpnook – Inbox</title>
<link href="https://fonts.googleapis.com/css2?family=Montserrat:wght@300;400;500;600&display=swap" rel="stylesheet">
<style>
:root{
  --blue:#0b8cf0;
  --green:#0aa80a;
  --orange:#f5a623;
  --ink:#1d1d1d;
  --muted:#a9a9a9;
  --line:#e6e6e6;
  --bg:#ffffff;
}
*{box-sizing:border-box;margin:0;padding:0}
html,body{width:1073px;height:1200px;overflow:hidden;background:var(--bg)}
body{font-family:"Montserrat",sans-serif;color:var(--ink);position:relative;font-size:12px}
.abs{position:absolute}
.topbar{left:0;top:0;width:1073px;height:57px;border-bottom:1px solid var(--line)}
.brand{left:20px;top:15px;display:flex;align-items:center;gap:7px;font-size:20px;font-weight:600;color:#444}
.brand-dot{width:18px;height:18px;border-radius:50%;background:#444}
.user{left:748px;top:6px;display:flex;align-items:center;gap:6px}
.avatar{border-radius:50%;display:block}
.user .avatar{width:42px;height:42px;border:3px solid var(--blue);background:radial-gradient(circle at 50% 40%,#d9a88a,#5c7a9a 70%)}
.user-name{font-size:12px;font-weight:600;line-height:1.2}
.user-status{font-size:11px;color:#888;font-weight:400}
.tool{top:0;height:57px;width:40px;display:flex;align-items:center;justify-content:center;border-left:1px solid var(--line)}
.menu-btn{left:1030px;top:15px;width:29px;height:27px;background:var(--blue);border-radius:3px;display:flex;align-items:center;justify-content:center}
.sidebar{left:0;top:57px;width:104px;height:1143px;border-right:1px solid var(--line)}
.nav-item{position:absolute;left:0;width:100px;text-align:center;font-size:11.5px;font-weight:400}
.nav-item svg{display:block;margin:0 auto 10px}
.notch{left:98px;top:190px;width:12px;height:12px;background:#fff;border-right:1px solid var(--line);border-top:1px solid var(--line);transform:rotate(45deg)}
.feedback{left:0;width:112px;text-align:center;font-size:11.5px;line-height:16px}
.page-title{left:122px;top:78px;display:flex;align-items:center;gap:12px;font-size:13px;font-weight:500}
.date{right:14px;top:79px;font-size:13px;font-weight:500}
.tabs{left:124px;top:111px;width:935px;height:53px;border:1px solid var(--line);display:flex}
.tab{height:51px;display:flex;align-items:center;justify-content:center;font-size:11.5px;font-weight:500}
.tab.active{width:112px;background:var(--green);color:#fff;margin:-1px 0 0 -1px;height:53px}
.msg{left:124px;width:935px;height:101px;border:1px solid var(--line)}
.msg-num{position:absolute;left:0;top:0;width:51px;height:99px;border-right:1px solid var(--line);display:flex;align-items:center;justify-content:center;font-size:21px;font-weight:300;color:var(--blue)}
.msg-num.new{color:var(--orange)}
.msg .avatar{position:absolute;left:76px;top:23px;width:55px;height:55px}
.msg-name{position:absolute;left:138px;top:34px;font-size:13px;font-weight:500}
.msg-text{position:absolute;left:138px;top:55px;font-size:10.5px;font-weight:300;color:var(--muted)}
.msg-time{position:absolute;right:13px;top:13px;font-size:11px;color:#555}
.chat-title{left:127px;top:710px;font-size:13px;font-weight:600;color:var(--blue)}
.chat-tools{left:344px;top:711px;display:flex;align-items:center;font-size:11.5px;color:#444}
.detail-tabs{right:14px;top:709px;display:flex;gap:14px;font-size:13px;font-weight:500}
.detail-tabs .sel{border-bottom:2px solid var(--blue);padding-bottom:4px}
.panel{top:758px;height:354px;border:1px solid var(--line)}
.chat-panel{left:124px;width:456px}
.chat-line{position:absolute;display:flex;gap:8px;align-items:flex-start}
.chat-line .avatar{width:55px;height:55px}
.chat-line b{display:block;font-size:13px;font-weight:500;margin-top:10px}
.chat-line span{display:block;font-size:11px;font-weight:300;color:var(--muted);margin-top:5px}
.composer{position:absolute;left:0;bottom:0;width:454px;height:70px;border-top:1px solid var(--line)}
.composer-input{position:absolute;left:18px;top:20px;font-size:12.5px;color:#888;font-weight:400}
.composer svg{position:absolute;right:24px;top:26px}
.detail-panel{left:604px;width:455px}
.detail-row{position:absolute;left:24px;display:flex;gap:20px;font-size:13px;font-weight:400;line-height:27px}
.detail-row svg{flex:none;margin-top:6px}
.detail-sub{font-size:11px;font-weight:300;color:var(--muted);line-height:14px}
.footer{left:104px;top:1153px;width:969px;height:47px;border-top:1px solid var(--line);text-align:center;font-size:11px;font-weight:500;line-height:47px;color:#222}
</style>
</head>
<body>
<header class="abs topbar">
  <div class="abs brand"><span class="brand-dot"></span>helpnook</div>
  <div class="abs user">
    <span class="avatar" role="img" aria-label="Agent profile photo"></span>
    <div><div class="user-name">Lena Varga</div><div class="user-status">Available</div></div>
  </div>
  <div class="abs tool" style="left:891px"><svg width="20" height="16" viewBox="0 0 20 16"><path d="M3 1h14l3 8v6H0V9z" fill="var(--blue)"/><path d="M3 9h4l1 2h4l1-2h4" stroke="#fff" stroke-width="1.6" fill="none"/></svg></div>
  <div class="abs tool" style="left:934px"><svg width="22" height="22" viewBox="0 0 22 22"><path d="M13 2l7 7-11 11-7-7z" fill="none" stroke="var(--blue)" stroke-width="2.4"/><path d="M9 9l4 4" stroke="var(--blue)" stroke-width="2"/></svg></div>
  <div class="abs tool" style="left:975px"><svg width="20" height="20" viewBox="0 0 20 20"><circle cx="10" cy="10" r="10" fill="var(--blue)"/><text x="10" y="15" font-size="13" font-weight="600" text-anchor="middle" fill="#fff" font-family="Montserrat,sans-serif">?</text></svg></div>
  <div class="abs tool" style="left:1018px;width:55px;border-left:1px solid var(--line)"></div>
  <div class="abs menu-btn"><svg width="12" height="10" viewBox="0 0 12 10"><path d="M0 1h12M0 5h12M0 9h12" stroke="#fff" stroke-width="2"/></svg></div>
</header>

<nav class="abs sidebar">
  <div class="nav-item" style="top:47px"><svg width="24" height="20" viewBox="0 0 24 20"><path d="M12 1a11 11 0 0 0-11 11v6h22v-6A11 11 0 0 0 12 1z" fill="var(--blue)"/><path d="M12 13l4-6" stroke="#fff" stroke-width="2"/><circle cx="12" cy="13" r="2" fill="#fff"/></svg>DASHBOARD</div>
  <div class="nav-item" style="top:119px"><svg width="20" height="18" viewBox="0 0 20 16"><path d="M3 1h14l3 8v6H0V9z" fill="var(--blue)"/><path d="M3 9h4l1 2h4l1-2h4" stroke="#fff" stroke-width="1.6" fill="none"/></svg>INBOX</div>
  <div class="nav-item" style="top:187px"><svg width="22" height="22" viewBox="0 0 22 22"><path d="M13 2l7 7-11 11-7-7z" fill="none" stroke="var(--blue)" stroke-width="2.4"/><path d="M9 9l4 4" stroke="var(--blue)" stroke-width="2"/></svg>TICKETS</div>
  <div class="nav-item" style="top:259px"><svg width="24" height="20" viewBox="0 0 24 20"><rect x="1" y="4" width="22" height="15" rx="2" fill="var(--blue)"/><path d="M8 4V1h8v3" stroke="var(--blue)" stroke-width="2" fill="none"/><path d="M1 10h22" stroke="#fff" stroke-width="1.5"/></svg>CLIENTS</div>
  <div class="nav-item" style="top:326px"><svg width="20" height="24" viewBox="0 0 20 24"><path d="M2 1h11l5 5v17H2z" fill="none" stroke="var(--blue)" stroke-width="2"/><path d="M6 11h8M6 15h8M6 19h8" stroke="var(--blue)" stroke-width="1.6"/></svg>REPORTS</div>
  <div class="nav-item" style="top:398px"><svg width="26" height="22" viewBox="0 0 26 22"><circle cx="9" cy="12" r="6" fill="none" stroke="var(--blue)" stroke-width="4" stroke-dasharray="3 2"/><circle cx="20" cy="6" r="4" fill="none" stroke="var(--blue)" stroke-width="3" stroke-dasharray="2 1.5"/><circle cx="20" cy="17" r="3" fill="none" stroke="var(--blue)" stroke-width="3" stroke-dasharray="2 1.5"/></svg>SETTINGS</div>
  <div class="abs feedback" style="top:1072px">SEND<br>FEEDBACK</div>
</nav>
<div class="abs notch"></div>

<main>
  <div class="abs page-title"><svg width="20" height="16" viewBox="0 0 20 16"><path d="M3 1h14l3 8v6H0V9z" fill="var(--blue)"/><path d="M3 9h4l1 2h4l1-2h4" stroke="#fff" stroke-width="1.6" fill="none"/></svg>INBOX</div>
  <div class="abs date">December 9th | 2017</div>

  <div class="abs tabs">
    <div class="tab active">AGENT</div>
    <div class="tab" style="width:148px">DEPARTMENT</div>
    <div class="tab" style="width:80px">ACCOUNT</div>
  </div>

  <article class="abs msg" style="top:176px"><div class="msg-num new">1</div><span class="avatar" role="img" aria-label="Customer photo" style="background:radial-gradient(circle at 50% 45%,#d8a98c,#4f7fa6 70%)"></span><div class="msg-name">Daniel Oakes</div><div class="msg-text">Neque porro quisquam est qui dolorem ipsum quia dolor sit amet, consectetur, adipisci velit...</div><div class="msg-time">2 Days Ago</div></article>
  <article class="abs msg" style="top:295px"><div class="msg-num">2</div><span class="avatar" role="img" aria-label="Customer photo" style="background:radial-gradient(circle at 50% 45%,#c99478,#3a3230 70%)"></span><div class="msg-name">Daniel Oakes</div><div class="msg-text">Neque porro quisquam est qui dolorem ipsum quia dolor sit amet, consectetur, adipisci velit...</div><div class="msg-time">2 Days Ago</div></article>
  <article class="abs msg" style="top:414px"><div class="msg-num">3</div><span class="avatar" role="img" aria-label="Customer photo" style="background:radial-gradient(circle at 50% 45%,#c9a08a,#5f8aaa 70%)"></span><div class="msg-name">Daniel Oakes</div><div class="msg-text">Neque porro quisquam est qui dolorem ipsum quia dolor sit amet, consectetur, adipisci velit...</div><div class="msg-time">2 Days Ago</div></article>
  <article class="abs msg" style="top:533px"><div class="msg-num">4</div><span class="avatar" role="img" aria-label="Customer photo" style="background:radial-gradient(circle at 50% 45%,#d4a68c,#4a3a38 70%)"></span><div class="msg-name">Daniel Oakes</div><div class="msg-text">Neque porro quisquam est qui dolorem ipsum quia dolor sit amet, consectetur, adipisci velit...</div><div class="msg-time">2 Days Ago</div></article>

  <div class="abs chat-title">ONLINE CHAT</div>
  <div class="abs chat-tools">
    <svg width="12" height="12" viewBox="0 0 12 12"><rect x="1" y="1" width="10" height="10" fill="none" stroke="var(--green)" stroke-width="1.8"/><rect x="3.5" y="1" width="5" height="3.5" fill="var(--green)"/></svg>
    <span style="margin-left:8px">Save Transcript</span>
    <svg style="margin-left:55px" width="11" height="11" viewBox="0 0 11 11"><path d="M1.5 1.5l8 8M9.5 1.5l-8 8" stroke="var(--green)" stroke-width="2.6"/></svg>
    <svg style="margin-left:20px" width="15" height="12" viewBox="0 0 15 12"><path d="M1 11c1-5 4-7 9-7V1l4 4.5L10 10V7C6 7 3 8 1 11z" fill="var(--blue)"/></svg>
    <svg style="margin-left:18px" width="13" height="13" viewBox="0 0 13 13"><circle cx="6.5" cy="6.5" r="5" fill="none" stroke="var(--blue)" stroke-width="1.8"/><path d="M3 10l7-7" stroke="var(--blue)" stroke-width="1.8"/></svg>
  </div>
  <div class="abs detail-tabs"><span class="sel">DETAILS</span><span>|</span><span>TICKETS</span><span>|</span><span>HISTORY</span></div>

  <section class="abs panel chat-panel">
    <div class="chat-line" style="left:24px;top:18px"><span class="avatar" role="img" aria-label="Customer photo" style="background:radial-gradient(circle at 50% 45%,#d4a68c,#4a3a38 70%)"></span><div><b>Daniel Oakes</b><span>Neque porro quisquam est qui dolorem...</span></div></div>
    <div class="chat-line" style="left:225px;top:106px"><span class="avatar" role="img" aria-label="Agent photo" style="background:radial-gradient(circle at 50% 45%,#c99478,#3a3230 70%)"></span><div><b>Perrin</b><span>Neque porro quisquam</span></div></div>
    <div class="composer"><div class="composer-input">Type Your Message Here ...</div><svg width="22" height="20" viewBox="0 0 22 20"><path d="M21 1L1 9l6 3 2 7 3-5 5 4z" fill="var(--blue)"/><path d="M21 1L7 12" stroke="#fff" stroke-width="1"/></svg></div>
  </section>

  <section class="abs panel detail-panel">
    <div class="detail-row" style="top:53px"><svg width="14" height="14" viewBox="0 0 14 14"><circle cx="7" cy="4" r="3.2" fill="var(--orange)"/><path d="M1 14c0-4 2.5-6 6-6s6 2 6 6z" fill="var(--orange)"/></svg><div><div>Daniel Oakes</div><div class="detail-sub">Neque porro quisquam est qui ...</div></div></div>
    <div class="detail-row" style="top:122px"><svg width="16" height="13" viewBox="0 0 16 13"><rect x="1" y="1" width="14" height="11" rx="1" fill="none" stroke="var(--blue)" stroke-width="1.6"/><path d="M1 2l7 5 7-5" stroke="var(--blue)" stroke-width="1.6" fill="none"/></svg><div>hello@danieloakes.io</div></div>
    <div class="detail-row" style="top:173px"><svg width="14" height="14" viewBox="0 0 14 14"><path d="M3 1l3 3-2 2c1 2 2 3 4 4l2-2 3 3-2 2C6 13 1 8 1 3z" fill="var(--blue)"/></svg><div>1-800-555-0147</div></div>
    <div class="detail-row" style="top:224px"><svg width="18" height="16" viewBox="0 0 18 16"><path d="M9 0l9 4H0z" fill="var(--blue)"/><path d="M2 6v7M6 6v7M12 6v7M16 6v7" stroke="var(--blue)" stroke-width="2"/><rect x="0" y="14" width="18" height="2" fill="var(--blue)"/></svg><div>Nordlicht Service<br>Lindenweg 12<br>20095 Hamburg</div></div>
  </section>
</main>

<footer class="abs footer">© 2017 Company Name &nbsp;| All Rights Reserved</footer>
</body>
</html>
```